Business card for law firm

Need business card for new law firm. Think confident, authoritative, conservative, but not stuffy or old-fashioned.

Contact Information for Business Card

Content for card - logo (uploaded), plus the following:

Paul Whitcombe (larger font)
Managing Partner (larger font, but not as large as name)
Level 9, 7 Ferris Lane
Sydney NSW 2000
Main Tel 02 9364 2710
Direct Tel 02 8472 3159
Email paul@qvlegal.com.au
www.qvlegal.com.au

Letterhead design should include logo plus:
Level 9, 7 Ferris Lane
Sydney NSW 2000
Tel 02 8472 3159
www.qvlegal.com.au

```html
<!DOCTYPE html>
<html lang="en">
<head>
<meta charset="utf-8">
<title>Quayvale Legal – Business Card</title>
<link rel="stylesheet" href="https://fonts.googleapis.com/css2?family=Source+Sans+3:wght@400;600;700&display=swap">
<style>
  :root {
    --navy: #001c54;
    --navy-soft: #0a2a66;
    --ink: #0d0d0d;
    --text: #2b2b2b;
    --rule: #c9c9c9;
    --paper: #fdfdfd;
    --backdrop: #cbcbcb;
  }
  * { margin: 0; padding: 0; box-sizing: border-box; }
  html, body { width: 1125px; height: 1200px; overflow: hidden; }
  body {
    background: var(--backdrop);
    font-family: "Source Sans 3", sans-serif;
    position: relative;
  }
  .card {
    position: absolute;
    left: 142px;
    width: 840px;
    height: 480px;
    background: var(--paper);
    overflow: hidden;
  }
  .card--front { top: 82px; }
  .card--back { top: 638px; }

  .brand {
    position: absolute;
    display: flex;
    flex-direction: column;
    align-items: center;
    color: var(--ink);
    font-weight: 600;
    text-transform: uppercase;
  }
  .brand__mark { background: var(--navy); }
  .brand__name { line-height: 1; letter-spacing: 0.02em; }
  .brand__sub { line-height: 1; }

  .card--front .brand { left: 76px; width: 300px; top: 134px; }
  .card--front .brand__mark { width: 76px; height: 96px; margin-bottom: 40px; }
  .card--front .brand__name { font-size: 46px; }
  .card--front .brand__sub { font-size: 19px; letter-spacing: 1.35em; margin-top: 10px; padding-left: 1.35em; }

  .card--back .brand { left: 0; width: 840px; top: 109px; }
  .card--back .brand__mark { width: 93px; height: 125px; margin-bottom: 33px; }
  .card--back .brand__name { font-size: 66px; }
  .card--back .brand__sub { font-size: 23px; letter-spacing: 1.7em; margin-top: 14px; padding-left: 1.7em; }

  .divider {
    position: absolute;
    left: 425px; top: 112px;
    width: 1px; height: 256px;
    background: var(--rule);
  }
  .contact {
    position: absolute;
    left: 469px; top: 106px;
    color: var(--text);
  }
  .contact__name {
    font-size: 27px; font-weight: 700; color: var(--navy);
    text-transform: uppercase; line-height: 1.1;
  }
  .contact__title { font-size: 22px; line-height: 1.2; }
  .contact__address { font-size: 22px; line-height: 28px; margin-top: 14px; font-style: normal; }
  .contact__list { list-style: none; margin-top: 16px; font-size: 22px; }
  .contact__list li { display: flex; align-items: center; height: 28px; }
  .contact__list svg { width: 17px; height: 17px; margin-right: 11px; fill: var(--navy); flex: none; }

  .footer-band {
    position: absolute;
    left: 0; bottom: 0;
    width: 840px; height: 52px;
    background: linear-gradient(180deg, var(--navy-soft), var(--navy));
  }
</style>
</head>
<body>

<section class="card card--front">
  <div class="brand">
    <span class="brand__mark"></span>
    <span class="brand__name">Quayvale</span>
    <span class="brand__sub">Legal</span>
  </div>

  <span class="divider"></span>

  <div class="contact">
    <p class="contact__name">Paul Whitcombe</p>
    <p class="contact__title">Managing Partner</p>
    <address class="contact__address">Level 9, 7 Ferris Lane<br>Sydney NSW 2000</address>
    <ul class="contact__list">
      <li><svg viewBox="0 0 24 24"><path d="M6.6 2.5l3 3.6-1.8 2.4c1 2.6 3.1 4.9 5.7 6.1l2.3-1.8 3.7 2.9-1.9 3.8C10.4 19 4.6 12.6 3 5z"/></svg>02 9364 2710 (Main)</li>
      <li><svg viewBox="0 0 24 24"><path d="M6.6 2.5l3 3.6-1.8 2.4c1 2.6 3.1 4.9 5.7 6.1l2.3-1.8 3.7 2.9-1.9 3.8C10.4 19 4.6 12.6 3 5z"/></svg>02 8472 3159 (Direct)</li>
      <li><svg viewBox="0 0 24 24"><path d="M2 9l10-6 10 6v12H2z M5 10l7 5 7-5" stroke="#fff" stroke-width="1.5"/></svg>paul@qvlegal.com.au</li>
      <li><svg viewBox="0 0 24 24"><circle cx="12" cy="12" r="9.5" fill="none" stroke="#001c54" stroke-width="2"/><path d="M12 2.5v19M2.5 12h19M4 7.5h16M4 16.5h16" stroke="#001c54" stroke-width="1.6" fill="none"/><ellipse cx="12" cy="12" rx="4.3" ry="9.5" fill="none" stroke="#001c54" stroke-width="1.6"/></svg>www.qvlegal.com.au</li>
    </ul>
  </div>

  <div class="footer-band" role="img" aria-label="Decorative navy wave band along the bottom edge"></div>
</section>

<section class="card card--back">
  <div class="brand">
    <span class="brand__mark"></span>
    <span class="brand__name">Quayvale</span>
    <span class="brand__sub">Legal</span>
  </div>
</section>

</body>
</html>
```